Harborline Claim Partners Business card

We need to get business card Design for our Company we are Public Adjusters in Chicago Illinois - i like to see good combination and elements from my Company Logo. as well To be an two side design
Updates

Target Market(s)

Home /Business owner Property Managers

Industry/Entity Type

Business

Contact Information for Business Card

to show the Element of our logo i will Like 3D

Font styles to use
Sans Serif

Requirements
Must have
• Logo and Element of the Logo in 3D
Nice to have
• Logo That we Provide 3D Same Colors or open for suggestions
Should not have
• unleare view -

```html
<!DOCTYPE html>
<html lang="en">
<head>
<meta charset="utf-8">
<title>Harborline Claim Partners – Business Card</title>
<link rel="stylesheet" href="https://fonts.googleapis.com/css2?family=Source+Sans+3:wght@400;600;700&display=swap">
<style>
  :root {
    --backdrop: #5b4a3b;
    --navy-deep: #0e0f44;
    --navy-mid: #16237a;
    --royal: #1f45c0;
    --paper: #ffffff;
    --brand-navy: #1a2a8c;
    --ink-grey: #555555;
    --card-shadow: 0 3px 8px rgba(0, 0, 0, 0.45);
  }
  * { box-sizing: border-box; margin: 0; padding: 0; }
  html, body {
    width: 1200px;
    height: 987px;
    overflow: hidden;
    background: var(--backdrop);
    font-family: "Source Sans 3", Arial, sans-serif;
  }
  .card {
    position: absolute;
    left: 293px;
    width: 614px;
    height: 350px;
    box-shadow: var(--card-shadow);
    overflow: hidden;
  }
  .card--front {
    top: 130px;
    background: radial-gradient(ellipse 75% 90% at 50% 88%, var(--royal) 0%, var(--navy-mid) 55%, var(--navy-deep) 100%);
  }
  .card--back {
    top: 505px;
    background: var(--paper);
  }
  .front-arc {
    position: absolute;
    left: 0;
    top: 0;
    width: 614px;
    height: 350px;
  }
  .front-brand {
    position: absolute;
    left: 0;
    top: 122px;
    width: 614px;
    text-align: center;
    font-size: 24px;
    font-weight: 700;
    color: var(--brand-navy);
  }
  .holder {
    position: absolute;
    left: 32px;
    top: 232px;
    color: var(--paper);
  }
  .holder__name {
    font-size: 21px;
    font-weight: 600;
    letter-spacing: 0.3px;
    line-height: 26px;
  }
  .holder__line {
    font-size: 16px;
    line-height: 23.5px;
  }
  .contacts {
    position: absolute;
    right: 30px;
    top: 233px;
    list-style: none;
    color: var(--paper);
  }
  .contacts__item {
    display: flex;
    justify-content: flex-end;
    align-items: center;
    gap: 7px;
    font-size: 16px;
    line-height: 23.5px;
  }
  .contacts__icon {
    width: 14px;
    height: 14px;
    fill: var(--paper);
    flex: none;
  }
  .back-brand {
    position: absolute;
    left: 0;
    top: 149px;
    width: 614px;
    display: flex;
    justify-content: center;
    align-items: center;
    gap: 12px;
  }
  .back-brand__dot {
    width: 40px;
    height: 40px;
    border-radius: 50%;
    background: var(--brand-navy);
  }
  .back-brand__name {
    font-size: 28px;
    font-weight: 700;
    color: var(--brand-navy);
  }
  .back-web {
    position: absolute;
    left: 0;
    top: 283px;
    width: 614px;
    text-align: center;
    font-size: 16px;
    letter-spacing: 2.6px;
    color: var(--ink-grey);
  }
</style>
</head>
<body>
  <section class="card card--front" aria-label="Business card front">
    <svg class="front-arc" viewBox="0 0 614 350" aria-hidden="true">
      <path d="M0 0 C 60 333, 554 333, 614 0 Z" fill="#ffffff"/>
    </svg>
    <div class="front-brand">Harborline Claim Partners</div>

    <div class="holder">
      <div class="holder__name">DANIEL REYES</div>
      <div class="holder__line">CEO/Founder</div>
      <div class="holder__line">2140 Linden Court</div>
      <div class="holder__line">Chicago, Illinois 60614</div>
    </div>

    <ul class="contacts">
      <li class="contacts__item">312 555 0148
        <svg class="contacts__icon" viewBox="0 0 24 24" aria-hidden="true"><path d="M6.6 10.8a15.1 15.1 0 0 0 6.6 6.6l2.2-2.2c.3-.3.7-.4 1-.2 1.1.4 2.3.6 3.6.6.6 0 1 .4 1 1V20c0 .6-.4 1-1 1C10.6 21 3 13.4 3 4c0-.6.4-1 1-1h3.5c.6 0 1 .4 1 1 0 1.3.2 2.5.6 3.6.1.3 0 .7-.2 1z"/></svg>
      </li>
      <li class="contacts__item">312 555 0172
        <svg class="contacts__icon" viewBox="0 0 24 24" aria-hidden="true"><path d="M7 1h10a2 2 0 0 1 2 2v18a2 2 0 0 1-2 2H7a2 2 0 0 1-2-2V3a2 2 0 0 1 2-2zm0 3v14h10V4zm5 15.2a1.2 1.2 0 1 0 0 2.4 1.2 1.2 0 0 0 0-2.4z"/></svg>
      </li>
      <li class="contacts__item">312 555 0196
        <svg class="contacts__icon" viewBox="0 0 24 24" aria-hidden="true"><path d="M6 2h12v6H6zM3 9h18a2 2 0 0 1 2 2v7h-4v4H5v-4H1v-7a2 2 0 0 1 2-2zm4 7v4h10v-4z"/></svg>
      </li>
      <li class="contacts__item">info@harborlineclaims.com
        <svg class="contacts__icon" viewBox="0 0 24 24" aria-hidden="true"><path d="M2 5h20v14H2zm2 2v.5l8 5.5 8-5.5V7z"/></svg>
      </li>
    </ul>
  </section>

  <section class="card card--back" aria-label="Business card back">
    <div class="back-brand">
      <span class="back-brand__dot" aria-hidden="true"></span>
      <span class="back-brand__name">Harborline Claim Partners</span>
    </div>
    <div class="back-web">www.HarborlineClaims.com</div>
  </section>
</body>
</html>
```